Business Cards for new orthopaedic surgery practice

My husband and I are starting our own orthopaedic surgery practice. We are looking for a business card that is uniform, but one will have my name/title and the other will have his. You can just create one design with my name on it for now. But when I choose your design as the winning design I will ask that you add another copy with his name/title.

We are looking for classy, simple, elite all in one. We like dark blues/a little gold/yellow. Something that goes with our logo. We want our logo incorporated. Here is all the info you need:
Business name: RV Bone & Vitality Center
Location: 38517 North Willowmere Ave
Cedar Brook, FL 33418
Phone: 954-218-4063
Fax: 954-582-7341
Email: info@myrvbonecare.example

Names: Lydia Vance, M.D.
Board Certified Hand and Upper Extremity Surgeon

Ebo Dansu, M.D.
Board Certified Hip & Knee Replacement/General Orthopaedic Surgeon

Can decide what you want to put on the back. Maybe a slogan:
Rooted in Care. Focused on You

I am just going to upload our logo. The only thing is if we select you as the winning design, the location, and phone numbers may change. We will need your help to update that once fully solidified.

Industry/Entity Type

Medical

Contact Information for Business Card

Colors
0054AA
0677BA
7BADD7
CADEEF
E8F1F8
0094D4
00A9DD
6FCCEA
C7EBF8
E9F6FB

Requirements
Must have
• class, appeal,
Should not have
• We want to air on the side of masculine if we are looking at masculine vs. feminine feel. But we still want it classy, sophisticated, and something we will love

```html
<!DOCTYPE html>
<html lang="en">
<head>
<meta charset="utf-8">
<title>RV Bone &amp; Vitality Center – Business Card</title>
<link rel="stylesheet" href="https://fonts.googleapis.com/css2?family=Montserrat:wght@400;500;700&display=swap">
<style>
  :root {
    --navy: #1b2a5e;
    --navy-deep: #14214d;
    --gold: #c9a55c;
    --ink: #1b2a5e;
    --text: #1d1d1f;
    --paper: #ffffff;
    --backdrop: #2b2b2d;
  }
  * { box-sizing: border-box; margin: 0; padding: 0; }
  html, body { width: 1200px; height: 875px; overflow: hidden; }
  body {
    background: var(--backdrop);
    font-family: "Montserrat", sans-serif;
    position: relative;
  }
  .card {
    position: absolute;
    width: 530px;
    height: 303px;
    border-radius: 18px;
    overflow: hidden;
  }
  .card-front {
    left: 50px; top: 150px;
    background: var(--navy);
  }
  .front-texture {
    position: absolute; inset: 0;
    background: linear-gradient(135deg, #22336c 0%, var(--navy) 50%, var(--navy-deep) 100%);
  }
  .front-emblem {
    position: absolute;
    left: 50%; top: 50%;
    width: 220px; height: 220px;
    transform: translate(-50%, -50%);
    border: 2px solid var(--gold);
    border-radius: 50%;
    display: flex; align-items: center; justify-content: center;
    text-align: center;
  }
  .front-name {
    color: #ffffff;
    font-weight: 500;
    font-size: 19px;
    line-height: 1.35;
    letter-spacing: 2px;
    text-transform: uppercase;
  }
  .card-back {
    left: 620px; top: 420px;
    background: var(--paper);
  }
  .back-brand {
    position: absolute;
    right: 30px; top: 22px;
    display: flex; align-items: center; gap: 10px;
  }
  .brand-dot {
    width: 54px; height: 54px;
    border: 1.5px solid var(--gold);
    border-radius: 50%;
  }
  .brand-name {
    color: var(--ink);
    font-weight: 500;
    font-size: 12px;
    line-height: 1.35;
    letter-spacing: 1.2px;
    text-transform: uppercase;
  }
  .person {
    position: absolute;
    left: 30px; top: 128px;
  }
  .person-name {
    font-weight: 700;
    font-size: 20px;
    color: var(--ink);
  }
  .person-name .credential { color: var(--gold); }
  .person-title {
    margin-top: 3px;
    font-size: 11.5px;
    line-height: 1.3;
    color: var(--text);
  }
  .rule {
    position: absolute;
    left: 30px; right: 30px; top: 200px;
    height: 1.5px;
    background: var(--gold);
  }
  .contacts {
    position: absolute;
    left: 30px; top: 212px;
    list-style: none;
    font-size: 12px;
    line-height: 1.55;
    color: var(--text);
  }
  .contacts li { display: flex; align-items: center; gap: 8px; }
  .contacts svg { width: 11px; height: 11px; fill: var(--gold); }
  .address {
    position: absolute;
    right: 30px; top: 212px;
    text-align: right;
    font-size: 12px;
    line-height: 1.55;
    color: var(--text);
  }
</style>
</head>
<body>
  <section class="card card-front">
    <div class="front-texture" role="img" aria-label="Subtle tone-on-tone navy pattern"></div>
    <div class="front-emblem">
      <p class="front-name">RV Bone &amp;<br>Vitality<br>Center</p>
    </div>
  </section>

  <section class="card card-back">
    <div class="back-brand">
      <span class="brand-dot"></span>
      <p class="brand-name">RV Bone &amp;<br>Vitality Center</p>
    </div>

    <div class="person">
      <p class="person-name">Lydia Vance, <span class="credential">M.D.</span></p>
      <p class="person-title">Board Certified Hand and<br>Upper Extremity Surgeon</p>
    </div>

    <div class="rule"></div>

    <ul class="contacts">
      <li>
        <svg viewBox="0 0 24 24" aria-hidden="true"><path d="M6.6 10.8a15.1 15.1 0 0 0 6.6 6.6l2.2-2.2a1 1 0 0 1 1-.25 11.4 11.4 0 0 0 3.6.57 1 1 0 0 1 1 1V20a1 1 0 0 1-1 1A17 17 0 0 1 3 4a1 1 0 0 1 1-1h3.5a1 1 0 0 1 1 1c0 1.25.2 2.45.57 3.57a1 1 0 0 1-.25 1z"/></svg>
        954-218-4063
      </li>
      <li>
        <svg viewBox="0 0 24 24" aria-hidden="true"><path d="M6 2h10v6H6zM4 9h16a2 2 0 0 1 2 2v7h-4v4H6v-4H2v-7a2 2 0 0 1 2-2zm4 8v3h8v-3z"/></svg>
        954-582-7341
      </li>
      <li>
        <svg viewBox="0 0 24 24" aria-hidden="true"><path d="M2 5h20v14H2zm2 2v.4l8 5.1 8-5.1V7z"/></svg>
        info@myrvbonecare.example
      </li>
    </ul>

    <p class="address">38517 North Willowmere Ave<br>Cedar Brook, FL 33418</p>
  </section>
</body>
</html>
```